Stationery Design Project

Please create a custom Stationery Design for Pinecrest Dwellings. The logo is attached to this brief.

Please Include:
- Letterhead
- With Compliments slip
- Envelope

Please also see open Business Card project: http://briefs.sketchvault.example/task.aspx?id=517290

Industry/Entity Type

Business

```html
<!DOCTYPE html>
<html lang="en">
<head>
<meta charset="utf-8">
<title>Pinecrest Dwellings – Stationery</title>
<link rel="stylesheet" href="https://fonts.googleapis.com/css2?family=Open+Sans:wght@400;600&display=swap">
<style>
  :root {
    --backdrop: #5d5d5d;
    --paper: #ffffff;
    --brand-blue: #0b6fbd;
    --brand-green: #6cbf3a;
    --ink: #555555;
    --faint: #e6e6e6;
    --rule: #b5b5b5;
  }
  * { box-sizing: border-box; margin: 0; padding: 0; }
  html, body { width: 1200px; height: 640px; overflow: hidden; }
  body {
    background: var(--backdrop);
    font-family: "Open Sans", sans-serif;
    color: var(--ink);
    position: relative;
  }
  .sheet { position: absolute; background: var(--paper); overflow: hidden; }

  .wordmark {
    display: flex; align-items: center; gap: 5px;
    color: var(--brand-blue); font-weight: 600; white-space: nowrap;
  }
  .wordmark .dot { width: 12px; height: 12px; border-radius: 50%; background: var(--brand-blue); flex: none; }

  .watermark { position: absolute; border-radius: 50%; background: var(--faint); }

  .contact { font-size: 5px; line-height: 1.6; color: var(--ink); }
  .contact-item { display: flex; align-items: center; gap: 3px; }
  .contact-item svg { width: 6px; height: 6px; flex: none; }
  .divided { border-left: 0.5px solid var(--rule); padding-left: 5px; }

  .base-band { position: absolute; left: 0; right: 0; bottom: 0; height: 6px; background: var(--brand-blue); }

  /* Letterhead */
  .letterhead { left: 56px; top: 40px; width: 414px; height: 560px; }
  .letterhead .wordmark { position: absolute; right: 30px; top: 44px; font-size: 13px; }
  .letterhead .watermark { left: 140px; top: 220px; width: 135px; height: 135px; }
  .letterhead .footer { position: absolute; left: 0; right: 0; bottom: 18px; text-align: center; }
  .letterhead .footer .row { display: flex; justify-content: center; gap: 8px; margin-bottom: 1px; }
  .letterhead .green-rule { position: absolute; left: 0; right: 0; bottom: 8px; height: 1.5px; background: var(--brand-green); }
  .letterhead .base-band { height: 6px; }

  /* Slip layouts */
  .slip .identity { position: absolute; left: 30px; bottom: 22px; display: flex; align-items: center; gap: 8px; }
  .slip .wordmark { font-size: 11px; margin-right: 4px; }
  .slip .watermark { width: 92px; height: 92px; }

  .dl-slip { left: 532px; top: 24px; width: 446px; height: 178px; }
  .dl-slip .watermark { right: 24px; top: 60px; }

  .envelope { left: 724px; top: 230px; width: 446px; height: 180px; }
  .envelope .flap {
    position: absolute; left: 0; top: 0; width: 100%; height: 52px;
    border-bottom: 0.8px solid var(--rule); border-radius: 0 0 28px 28px;
  }
  .envelope .flap-mark {
    position: absolute; left: 50%; top: 14px; transform: translateX(-50%);
    width: 22px; height: 22px; border-radius: 50%; background: var(--brand-blue);
  }

  .comp-slip { left: 580px; top: 438px; width: 368px; height: 162px; }
  .comp-slip .heading {
    position: absolute; right: 26px; top: 16px;
    font-size: 12px; color: var(--brand-blue); font-weight: 400;
  }
  .comp-slip .watermark { right: 22px; top: 60px; width: 82px; height: 82px; }
  .comp-slip .identity { left: 22px; bottom: 22px; gap: 6px; }
  .comp-slip .wordmark { font-size: 9.5px; }
  .comp-slip .contact { font-size: 4.5px; }
</style>
</head>
<body>

<svg width="0" height="0" style="position:absolute" aria-hidden="true">
  <defs>
    <symbol id="icon-phone" viewBox="0 0 10 10">
      <rect width="10" height="10" rx="1.5" fill="#0b6fbd"/>
      <path d="M3 2.5 L4.2 2.5 L4.6 4 L3.9 4.5 Q4.5 5.8 5.5 6.2 L6 5.5 L7.5 5.9 L7.5 7.1 Q4 7.3 3 2.5 Z" fill="#fff"/>
    </symbol>
    <symbol id="icon-web" viewBox="0 0 10 10">
      <rect width="10" height="10" rx="1.5" fill="#0b6fbd"/>
      <circle cx="5" cy="5" r="2.8" fill="none" stroke="#fff" stroke-width="0.8"/>
      <path d="M2.2 5 H7.8 M5 2.2 Q3.5 5 5 7.8 M5 2.2 Q6.5 5 5 7.8" fill="none" stroke="#fff" stroke-width="0.6"/>
    </symbol>
  </defs>
</svg>

<section class="sheet letterhead" aria-label="Letterhead">
  <div class="wordmark"><span class="dot"></span>Pinecrest Dwellings</div>
  <div class="watermark" aria-hidden="true"></div>
  <div class="footer contact">
    <div class="row">
      <span class="contact-item"><svg><use href="#icon-phone"/></svg>020 7946 0321</span>
      <span class="contact-item"><svg><use href="#icon-web"/></svg>www.pinecrest.example</span>
    </div>
    <div>12 Alder Court, Address Line, Fenwick Business Park, City Name</div>
  </div>
  <div class="green-rule"></div>
  <div class="base-band"></div>
</section>

<section class="sheet slip dl-slip" aria-label="Compliments card">
  <div class="watermark" aria-hidden="true"></div>
  <div class="identity">
    <div class="wordmark"><span class="dot"></span>Pinecrest Dwellings</div>
    <div class="contact divided">
      <div>12 Alder Court, Address Line</div>
      <div>Fenwick Business Park, City Name</div>
    </div>
  </div>
  <div class="base-band"></div>
</section>

<section class="sheet envelope" aria-label="Envelope back">
  <div class="flap"></div>
  <div class="flap-mark" aria-hidden="true"></div>
</section>

<section class="sheet slip comp-slip" aria-label="With compliments slip">
  <h2 class="heading">With Compliments</h2>
  <div class="watermark" aria-hidden="true"></div>
  <div class="identity">
    <div class="wordmark"><span class="dot"></span>Pinecrest Dwellings</div>
    <div class="contact divided">
      <div>12 Alder Court, Address Line</div>
      <div>Fenwick Business Park, City Name</div>
    </div>
    <div class="contact divided">
      <div class="contact-item"><svg><use href="#icon-phone"/></svg>020 7946 0321</div>
      <div class="contact-item"><svg><use href="#icon-web"/></svg>www.pinecrest.example</div>
    </div>
  </div>
  <div class="base-band"></div>
</section>

</body>
</html>
```